RevelHubQZ Business Cards

Front
Has logo with a design. Website address (www.revelhubqz-example.net)
Has slogan (discover the nightlife)
Has phone number (5182297734)
Should be bold and stands out.

Back
Has details about what we offer.

Events
Search upcoming events
Submit events
Party Image Gallery
View and download HQ party images
Sign up as a contributing event photographer and get paid!
Tickets
Sell your event tickets online for free!
Direct pay
No ticket fee

Target Market(s)

These cards will be handed out in clubs and events to patrons.

Industry/Entity Type

Business

Contact Information for Business Card

Should match or mirror our website in some sort of way. Visit the website to get ideas.

Requirements
Must have
• Must be designed for a 3x3 inch card.

```html
<!DOCTYPE html>
<html lang="en">
<head>
<meta charset="utf-8">
<title>RevelHubQZ Business Cards</title>
<link href="https://fonts.googleapis.com/css2?family=Open+Sans:wght@400;600;700&family=Nunito:wght@400;700&display=swap" rel="stylesheet">
<style>
  :root {
    --backdrop: #2f2f2f;
    --card: #ffffff;
    --blue: #2fa3d8;
    --pink: #e03d91;
    --ink: #3a3a3a;
    --muted: #555555;
  }
  * { margin: 0; padding: 0; box-sizing: border-box; }
  html, body { width: 1200px; height: 750px; overflow: hidden; }
  body {
    background: var(--backdrop);
    position: relative;
    font-family: "Open Sans", sans-serif;
  }
  .card {
    position: absolute;
    top: 166px;
    width: 416px;
    height: 416px;
    background: var(--card);
    text-align: center;
  }
  .card--front { left: 170px; }
  .card--back { left: 619px; }

  .hero-art {
    position: absolute;
    left: 12px;
    top: 0;
    width: 392px;
    height: 214px;
    border-radius: 0 0 60px 60px;
    background: linear-gradient(180deg, #e9f5fb 0%, #d3ebf7 70%, #f7dcea 100%);
  }

  .brand {
    display: flex;
    align-items: center;
    justify-content: center;
    gap: 10px;
    font-family: "Open Sans", sans-serif;
    font-weight: 600;
    color: var(--blue);
  }
  .brand__mark {
    width: 18px;
    height: 18px;
    background: var(--pink);
  }
  .tagline {
    font-family: "Open Sans", sans-serif;
    font-size: 10px;
    letter-spacing: 6px;
    color: var(--ink);
    text-transform: lowercase;
  }

  .card--front .brand { position: absolute; left: 0; right: 0; top: 238px; font-size: 30px; }
  .card--front .tagline { position: absolute; left: 0; right: 0; top: 272px; }
  .phone {
    position: absolute; left: 0; right: 0; top: 294px;
    font-size: 50px; font-weight: 700; color: var(--blue); letter-spacing: 1px;
  }
  .website {
    position: absolute; left: 0; right: 0; top: 356px;
    font-size: 19px; font-weight: 600; color: var(--pink);
  }

  .card--back .brand { position: absolute; left: 0; right: 0; top: 60px; font-size: 32px; }
  .card--back .tagline { position: absolute; left: 0; right: 0; top: 100px; }

  .offer {
    position: absolute; left: 0; right: 0; top: 260px;
    font-family: "Nunito", sans-serif;
  }
  .offer__title {
    display: flex; align-items: center; gap: 4px;
    padding: 0 44px;
    font-size: 17px; font-weight: 700; color: var(--blue);
  }
  .offer__title::before, .offer__title::after {
    content: ""; flex: 1; height: 1px;
    background: linear-gradient(90deg, rgba(224,61,145,0), var(--pink));
  }
  .offer__title::after { background: linear-gradient(90deg, var(--pink), rgba(224,61,145,0)); }
  .offer__list { list-style: none; margin-top: 10px; font-size: 13.4px; line-height: 17.5px; color: var(--muted); }
  .dot {
    display: inline-block; width: 5px; height: 5px; border-radius: 50%;
    background: var(--blue); vertical-align: middle; margin: 0 2px 2px;
  }
</style>
</head>
<body>
  <section class="card card--front">
    <div class="hero-art" role="img" aria-label="Decorative music artwork area in blue and pink"></div>
    <div class="brand"><span class="brand__mark"></span>RevelHubQZ</div>
    <p class="tagline">discover the nightlife</p>
    <p class="phone">5182297734</p>
    <p class="website">www.revelhubqz-example.net</p>
  </section>

  <section class="card card--back">
    <div class="brand"><span class="brand__mark"></span>RevelHubQZ</div>
    <p class="tagline">discover the nightlife</p>
    <div class="offer">
      <h2 class="offer__title">Events</h2>
      <ul class="offer__list">
        <li>Search upcoming events<span class="dot"></span>Submit events</li>
        <li>Party Image Gallery<span class="dot"></span>View &amp; download HQ party images</li>
        <li>Sign up as a contributing event photographer &amp; get paid!</li>
        <li>Tickets<span class="dot"></span>Sell your event tickets online for free!</li>
        <li>Direct pay<span class="dot"></span>No ticket fee</li>
      </ul>
    </div>
  </section>
</body>
</html>
```